Brightwave Reach - Business Card

We need a business card for a Social Media Marketing company that specializes in online marketing for small businesses in Canada using common Social Media platforms such as Pixlora, Chatterly, Blinkpost & Quibber.

I have uploaded a copy of our logo which I would like utilized in the business card. We would like the business card to be modern yet classy design.

Our website is www.brightwavereach.ca

Industry/Entity Type

Marketing

Contact Information for Business Card

Email: info@brightwavereach.ca
Website: www.brightwavereach.ca
Telephone: 604-555-0193

Colors

Designer to choose colors to be used in the design.

Requirements
Must have
• Social Media icons on reverse
• Please add some designs with color.

```html
<!DOCTYPE html>
<html lang="en">
<head>
<meta charset="UTF-8">
<title>Brightwave Reach – Business Card</title>
<link href="https://fonts.googleapis.com/css2?family=Lato:wght@400;700;900&display=swap" rel="stylesheet">
<style>
  :root {
    --stage: #e4e4e4;
    --charcoal: #3b3e40;
    --ink: #2a2a2a;
    --black: #111111;
    --paper: #ffffff;
    --rule: #333333;
  }
  * { box-sizing: border-box; margin: 0; padding: 0; }
  html, body { width: 1200px; height: 900px; overflow: hidden; }
  body {
    background: var(--stage);
    font-family: "Lato", Arial, sans-serif;
    display: flex;
    flex-direction: column;
    align-items: center;
    justify-content: center;
    gap: 40px;
  }
  .card {
    position: relative;
    width: 630px;
    height: 360px;
    box-shadow: 0 10px 28px rgba(0,0,0,0.25);
    overflow: hidden;
  }

  /* Back */
  .card-back { background: var(--charcoal); color: var(--paper); }
  .card-back .brand {
    position: absolute;
    top: 90px; left: 0; right: 0;
    display: flex; align-items: center; justify-content: center; gap: 14px;
  }
  .brand-mark { width: 26px; height: 26px; border: 3px solid currentColor; }
  .brand-name {
    font-weight: 900; font-size: 38px; letter-spacing: 1px; text-transform: uppercase;
  }
  .social-row {
    position: absolute;
    left: 40px; right: 40px; bottom: 70px;
    display: flex; justify-content: space-between;
  }
  .social {
    display: flex; flex-direction: column; align-items: center; gap: 8px;
    font-size: 14px; font-weight: 700;
  }
  .social-tile { width: 44px; height: 44px; border-radius: 8px; background: var(--paper); }

  /* Front */
  .card-front { background: var(--paper); color: var(--ink); }
  .card-front .brand {
    position: absolute; top: 40px; left: 44px;
    display: flex; align-items: center; gap: 12px; color: var(--charcoal);
  }
  .card-front .brand-name { font-size: 30px; }
  .card-front .brand-mark { width: 22px; height: 22px; }
  .divider {
    position: absolute; top: 118px; left: 44px; right: 44px;
    border-top: 1.5px solid var(--rule);
  }
  .phone {
    position: absolute; top: 140px; left: 44px;
    display: flex; align-items: center; gap: 10px; font-size: 18px;
  }
  .person {
    position: absolute; top: 180px; right: 44px; text-align: right;
  }
  .person-name { font-weight: 900; font-size: 26px; color: var(--ink); }
  .person-title { font-size: 17px; margin-top: 2px; }
  .person-rule {
    width: 260px; margin-left: auto; margin-top: 8px;
    border-top: 1.5px solid var(--rule);
  }
  .email {
    position: absolute; top: 262px; right: 44px;
    display: flex; align-items: center; gap: 10px; font-size: 18px;
  }
  .footer-bands { position: absolute; left: 0; bottom: 0; width: 630px; height: 56px; }
  .website {
    position: absolute; right: 44px; bottom: 14px;
    color: var(--paper); font-size: 19px; letter-spacing: 0.3px;
  }
  .icon { width: 16px; height: 16px; fill: var(--ink); }
</style>
</head>
<body>

  <section class="card card-back" aria-label="Card reverse">
    <div class="brand">
      <span class="brand-mark"></span>
      <span class="brand-name">Brightwave Reach</span>
    </div>
    <div class="social-row">
      <div class="social"><span class="social-tile"></span>Chatterly</div>
      <div class="social"><span class="social-tile"></span>Pixlora</div>
      <div class="social"><span class="social-tile"></span>Quibber</div>
      <div class="social"><span class="social-tile"></span>Blinkpost</div>
    </div>
  </section>

  <section class="card card-front" aria-label="Card front">
    <div class="brand">
      <span class="brand-mark"></span>
      <span class="brand-name">Brightwave Reach</span>
    </div>
    <div class="divider"></div>

    <div class="phone">
      <svg class="icon" viewBox="0 0 24 24" aria-hidden="true"><path d="M6.6 10.8a15 15 0 0 0 6.6 6.6l2.2-2.2a1 1 0 0 1 1-.25 11.4 11.4 0 0 0 3.6.57 1 1 0 0 1 1 1V20a1 1 0 0 1-1 1A17 17 0 0 1 3 4a1 1 0 0 1 1-1h3.5a1 1 0 0 1 1 1c0 1.25.2 2.45.57 3.57a1 1 0 0 1-.25 1z"/></svg>
      <span>604-555-0193</span>
    </div>

    <div class="person">
      <div class="person-name">Daniel Ferris</div>
      <div class="person-title">Manager</div>
      <div class="person-rule"></div>
    </div>

    <div class="email">
      <svg class="icon" viewBox="0 0 24 24" aria-hidden="true"><path d="M2 5h20v14H2z M2 5l10 8 10-8" fill="none" stroke="#2a2a2a" stroke-width="2"/></svg>
      <span>info@brightwavereach.ca</span>
    </div>

    <svg class="footer-bands" viewBox="0 0 630 56" aria-hidden="true">
      <polygon points="0,38 240,38 220,56 0,56" fill="#111111"/>
      <path d="M228,56 C250,30 270,10 320,8 L630,8 L630,56 Z" fill="#3b3e40"/>
      <path d="M212,56 C236,26 262,4 320,2 L330,2 C268,6 246,28 224,56 Z" fill="#3b3e40"/>
    </svg>
    <div class="website">www.brightwavereach.ca</div>
  </section>

</body>
</html>
```